Brightfen Business Card Redesign & Logo Update

We need to update our business cards to something more modern and fresh. Brightfen can provide the current color schemes and old design examples, but welcome creativity in helping us with this redesign. PLEASE NOTE that we no longer utilize the "tree" and/or "leaf" imagery in our branding. If able would apprecaite an update on the quality of our "words only" logo in Ai. / PNG formats too.

Target Market(s)

Investors, landowners, corporate partners, contractors

Industry/Entity Type

Environmental Restoration & Conservation

Contact Information for Business Card

Logo, persons name, title, mailing address, phone and email, website url

Font styles to use
Other font styles liked:
• Merriweather

Requirements
Nice to have
• Logo, persons name, title, mailing address, phone and email, website url, but open to ideams
Should not have
• No all back backgrounds

```html
<!DOCTYPE html>
<html lang="en">
<head>
<meta charset="utf-8">
<title>Brightfen Business Card</title>
<link rel="stylesheet" href="https://fonts.googleapis.com/css2?family=Oswald:wght@500;600&family=Roboto:wght@400&display=swap">
<style>
  :root {
    --bg: #e6e7e4;
    --paper: #ffffff;
    --green: #0f8436;
    --green-pattern: #12883a;
    --orange: #ef7d0c;
    --ink: #1b1b1b;
    --rule: #8c8c8c;
  }
  * { box-sizing: border-box; margin: 0; padding: 0; }
  html, body { width: 1200px; height: 1108px; overflow: hidden; }
  body {
    background: var(--bg);
    display: flex; align-items: center; justify-content: center; gap: 70px;
    font-family: "Roboto", sans-serif;
  }
  .card {
    width: 420px; height: 720px; border-radius: 26px;
    position: relative; overflow: hidden;
    box-shadow: 0 10px 30px rgba(0,0,0,.18);
  }
  .card-front {
    background: var(--paper);
    display: flex; flex-direction: column; align-items: center;
  }
  .brand { margin-top: 150px; text-align: center; }
  .brand-name {
    font-family: "Oswald", sans-serif; font-weight: 600;
    font-size: 84px; line-height: 1; letter-spacing: -1px;
    color: var(--green); text-transform: uppercase;
  }
  .brand-tagline {
    font-family: "Oswald", sans-serif; font-weight: 500;
    font-size: 20.5px; color: var(--ink); text-transform: uppercase;
    letter-spacing: -0.2px; margin-top: 2px;
  }
  .person { margin-top: 150px; text-align: center; }
  .person-name {
    font-family: "Oswald", sans-serif; font-weight: 600;
    font-size: 38px; line-height: 1.05; text-transform: uppercase;
  }
  .person-name .first { color: var(--orange); }
  .person-name .last { color: var(--green); }
  .person-title {
    font-family: "Oswald", sans-serif; font-weight: 500;
    font-size: 20px; color: var(--ink); text-transform: uppercase;
  }
  .icon-row {
    display: flex; align-items: center; gap: 8px; margin-top: 16px; width: 300px;
  }
  .icon-row .rule { flex: 1; height: 1px; background: var(--rule); }
  .icon {
    width: 34px; height: 34px; border-radius: 6px; background: var(--orange);
    display: flex; align-items: center; justify-content: center;
  }
  .contact { margin-top: 14px; text-align: center; font-size: 18px; line-height: 1.4; color: var(--ink); }
  .divider { width: 300px; height: 1px; background: var(--rule); margin: 14px 0; }
  .address { text-align: center; font-size: 18px; line-height: 1.4; color: var(--ink); }
  .card-back { background: var(--green); }
  .back-pattern { position: absolute; inset: 0; background: linear-gradient(135deg, #169a45 0%, var(--green-pattern) 50%, #0c7530 100%); }
  .back-brand {
    position: absolute; inset: 0; display: flex; align-items: center; justify-content: center;
    font-family: "Oswald", sans-serif; font-weight: 600; font-size: 40px;
    color: var(--paper); text-transform: uppercase; letter-spacing: -0.5px;
  }
</style>
</head>
<body>
  <section class="card card-front">
    <div class="brand">
      <div class="brand-name">Brightfen</div>
      <div class="brand-tagline">Environmental Credit Company</div>
    </div>
    <div class="person">
      <div class="person-name"><span class="first">Daniel</span> <span class="last">Harper</span></div>
      <div class="person-title">Managing Director</div>
    </div>
    <div class="icon-row">
      <span class="rule"></span>
      <span class="icon"><svg width="20" height="20" viewBox="0 0 24 24" fill="#fff"><path d="M6.6 10.8a15 15 0 0 0 6.6 6.6l2.2-2.2a1 1 0 0 1 1-.25 11.4 11.4 0 0 0 3.6.6 1 1 0 0 1 1 1V20a1 1 0 0 1-1 1A17 17 0 0 1 3 4a1 1 0 0 1 1-1h3.5a1 1 0 0 1 1 1c0 1.25.2 2.45.6 3.6a1 1 0 0 1-.25 1z"/></svg></span>
      <span class="icon"><svg width="20" height="20" viewBox="0 0 24 24" fill="none" stroke="#fff" stroke-width="2"><rect x="3" y="5" width="18" height="14" rx="1"/><path d="M3 6l9 7 9-7"/></svg></span>
      <span class="icon"><svg width="20" height="20" viewBox="0 0 24 24" fill="none" stroke="#fff" stroke-width="2"><circle cx="12" cy="12" r="9"/><path d="M3 12h18M12 3a14 14 0 0 1 0 18M12 3a14 14 0 0 0 0 18"/></svg></span>
      <span class="rule"></span>
    </div>
    <div class="contact">
      <div>044-555 010 234</div>
      <div>hello@brightfen.com</div>
      <div>www.brightfen.com</div>
    </div>
    <div class="divider"></div>
    <div class="address">
      <div>421, Address line goes here</div>
      <div>45452,Country Name</div>
    </div>
  </section>
  <section class="card card-back">
    <div class="back-pattern" role="img" aria-label="Diagonal repeated brand-name pattern in tonal greens"></div>
    <div class="back-brand">Brightfen</div>
  </section>
</body>
</html>
```